Stationery Design Project

I need a stationary design for our company. we are based in Houston, TX and we are called Mira Vell Lending. And we are wanting to brand our MoneyMendPlus program, which includes our tax preparation and restoration, credit repair service. Although our business offers other programs, we are interested in mainly focusing on The MoneyMendPlus program. We are looking for way to brand our ourselves and I believe that a great stationery design will help in achieving this goal. Our logo design is blue and light blue. the slogan is orange.

Industry/Entity Type

Business

Requirements
Must have
• Address: 30871 Calloway Ln. B-22
Houston, TX 75419
Tel. 555-318-6207
Fax 555-294-7153
www.miravelllending.example
info@miravelllending.example
Our Slogan: Happiness, Restored!

```html
<!DOCTYPE html>
<html lang="en">
<head>
<meta charset="utf-8">
<title>Mira Vell Lending – MoneyMendPlus Business Cards</title>
<link rel="stylesheet" href="https://fonts.googleapis.com/css2?family=Libre+Baskerville:wght@400&family=Open+Sans:wght@400&display=swap">
<style>
  :root {
    --navy: #143e64;
    --blue: #1c5f9c;
    --sky: #2f8fd0;
    --frame: #c3d6ea;
    --orange: #f29a1f;
    --ink: #2d2d2d;
    --paper: #ffffff;
    --backdrop: #ebe8e4;
    --serif: "Libre Baskerville", "Times New Roman", serif;
    --sans: "Open Sans", Arial, sans-serif;
  }
  * { margin: 0; padding: 0; box-sizing: border-box; }
  html, body { width: 1200px; height: 800px; overflow: hidden; }
  body { background: var(--backdrop); font-family: var(--sans); color: var(--ink); }
  .sheet { position: relative; width: 1200px; height: 800px; }

  .side-label {
    position: absolute; width: 510px; text-align: center;
    font-size: 21px; color: #222;
  }

  .card {
    position: absolute; width: 510px; height: 290px;
    border-radius: 22px; overflow: hidden;
    box-shadow: 0 4px 10px rgba(0,0,0,.25);
  }
  .card--light { background: var(--paper); }
  .card--dark { background: var(--navy); }

  /* Front */
  .program-name {
    position: absolute; left: 0; right: 0; top: 105px; text-align: center;
    font-family: var(--serif); font-size: 38px; color: var(--blue);
  }
  .contact-list {
    position: absolute; left: 58px; top: 168px; list-style: none;
    font-size: 13px; line-height: 17px;
  }
  .contact-list li { display: flex; align-items: center; gap: 6px; }
  .contact-list svg { width: 11px; height: 11px; flex: none; }
  .address {
    position: absolute; left: 274px; top: 204px;
    font-size: 13px; line-height: 18px; font-style: normal;
  }
  .front-swoosh { position: absolute; left: 0; bottom: 0; width: 510px; height: 50px; }
  .slogan {
    position: absolute; right: 72px; bottom: 8px;
    font-family: var(--serif); font-variant: small-caps; font-size: 20px;
    color: var(--orange); letter-spacing: .5px;
  }

  /* Backs */
  .brand-box {
    position: absolute; background: var(--navy);
    display: flex; align-items: flex-end; justify-content: center;
  }
  .brand-box--solid { left: 172px; top: 33px; width: 170px; height: 170px; border: 2px solid var(--paper); outline: 2px solid var(--frame); padding-bottom: 28px; }
  .brand-box--outline { left: 170px; top: 35px; width: 170px; height: 170px; border: 3px solid var(--frame); padding-bottom: 30px; }
  .company-name { font-family: var(--serif); color: var(--paper); font-size: 13px; }
  .company-name--large {
    position: absolute; left: 0; right: 0; top: 183px; text-align: center; font-size: 19px;
  }
  .web {
    position: absolute; left: 0; right: 0; text-align: center;
    font-size: 19px; letter-spacing: 2.6px;
  }
  .card--light .web { top: 237px; color: #333; }
  .card--dark .web { top: 250px; color: var(--paper); }
</style>
</head>
<body>
<main class="sheet">

  <p class="side-label" style="left:70px; top:50px;">Front</p>
  <p class="side-label" style="left:620px; top:50px;">Back - 1</p>
  <p class="side-label" style="left:75px; top:410px;">Back - 2</p>
  <p class="side-label" style="left:620px; top:410px;">Back - 3</p>

  <!-- Front -->
  <section class="card card--light" style="left:70px; top:90px;">
    <p class="program-name">MoneyMendPlus</p>
    <ul class="contact-list">
      <li><svg viewBox="0 0 12 12"><path d="M3 1l2 3-1 1c1 2 2 3 3 3l1-1 3 2-1 2C5 11 1 7 1 2z" fill="#333"/></svg>555-318-6207</li>
      <li><svg viewBox="0 0 12 12"><rect x="1" y="5" width="10" height="6" fill="#333"/><rect x="3" y="1" width="6" height="4" fill="#333"/></svg>555-294-7153</li>
      <li><svg viewBox="0 0 12 12"><rect x="1" y="3" width="10" height="7" fill="none" stroke="#333" stroke-width="1.4"/><path d="M1 3l5 4 5-4" fill="none" stroke="#333" stroke-width="1.2"/></svg>info@miravelllending.example</li>
      <li><svg viewBox="0 0 12 12"><circle cx="6" cy="6" r="5" fill="none" stroke="#333" stroke-width="1.2"/><path d="M1 6h10M6 1c-3 3-3 7 0 10M6 1c3 3 3 7 0 10" fill="none" stroke="#333" stroke-width=".9"/></svg>www.miravelllending.example</li>
    </ul>
    <address class="address">30871 Calloway Ln. B-22<br>Houston, TX 75419</address>
    <svg class="front-swoosh" viewBox="0 0 510 50" preserveAspectRatio="none" aria-hidden="true">
      <defs>
        <linearGradient id="bandFill" x1="0" x2="1">
          <stop offset="0" stop-color="#1c4f86"/>
          <stop offset="1" stop-color="#2f8fd0"/>
        </linearGradient>
      </defs>
      <path d="M0 38 C120 12 300 -2 510 20 L510 50 L0 50 Z" fill="url(#bandFill)"/>
      <path d="M0 34 C90 14 180 6 300 6 C180 12 80 26 0 44 Z" fill="var(--orange)"/>
      <path d="M0 44 C80 26 180 12 300 6 C200 14 100 28 0 48 Z" fill="#ffffff"/>
    </svg>
    <p class="slogan">Happiness, Restored!</p>
  </section>

  <!-- Back 1 -->
  <section class="card card--light" style="left:620px; top:90px;">
    <div class="brand-box brand-box--solid"><span class="company-name">Mira Vell Lending</span></div>
    <p class="web">www.miravelllending.example</p>
  </section>

  <!-- Back 2 -->
  <section class="card card--dark" style="left:75px; top:450px;">
    <p class="company-name company-name--large">Mira Vell Lending</p>
    <p class="web">www.miravelllending.example</p>
  </section>

  <!-- Back 3 -->
  <section class="card card--dark" style="left:620px; top:450px;">
    <div class="brand-box brand-box--outline"><span class="company-name">Mira Vell Lending</span></div>
    <p class="web">www.miravelllending.example</p>
  </section>

</main>
</body>
</html>
```